Wordpress Design Project

Hi- We are seeking a Wordpress Theme Design that will best serve as an introduction of our company, Tesh Kalo Trading Co, to potential international clients on the web.

We are a relationship management company that help build connections between professional music equipment manufacturers and high-volume professional music equipment users, i.e concert venue managers, equipment resellers, club owners, djs,etc.

We would like to see designs to incorporate the following:

- If possible a music theme tastefully designed into the company name/logo on the wordpress home page (not a dealbreaker without)

-We are choosing the Wordpress CMS because we're looking for the site to be more centered around our blog, which will be the main medium where we connect with clients and potential clients, where these previously strangers that we meet briefly on our travelings can get to know us better by coming to the site. The relationship, and the rapport that they feel towards my team and I, will be the key driver in determining whether they will want to do business through us or not. The products are secondary in importance. It is after the visitor feel comfortable doing business through us that they will venture to check out the products that we offer. Finally, the website is not a sales point, there will not be a feature for someone to buy something from the site.

Long story short, this website is meant to be a communications channel and not a sales channel.

-Need a contacts form application built-in to capture interested client information to facilitate the off-site sales process.

- Would prefer the theme to give a minimalist and conservative feel, and ideally capture the concept of our globalized world and the synergizing role that music plays in bringing people together.

-Ideally the design should incorporate subtle references to the Generation Y values that inspired our company name and mission:

-Emphasis on partnership and teamwork
-Belief and aspiration for win/win trade relations
-Fast, honest, and transparent service
-Make the world a better place via trade

Theme example (function-wise): http://demo2.plorvexthemes.com/?name=brit

Product Type examplex: http://www.kavro.com.cn/en/product.asp

(Willing to pay extra if the winning design can be coded to full functionality)
Updates

To all those designers who've accepted the contest invitation, can you please send me a quick message to confirm if you are still planning on submitting by the end of the day tomorrow, 8/9. Otherwise we will make a selection ahead of the deadline so we can speed up our website live date. Thanks!

Target Market(s)

High volume/frequency professional music equipment users/resellers. Concert venues, DJs, Dance Clubs, etc

Industry/Entity Type

Communications

Requirements
Must have
• Blog
Product Showcase Page that is easy to update and expand.
About Page
Contact Forms Application built-in
Nice to have
• Music theme designed into company name/logo

```html
<!DOCTYPE html>
<html lang="en">
<head>
<meta charset="utf-8">
<title>Tesh Kalo Trading Co</title>
<link rel="stylesheet" href="https://fonts.googleapis.com/css2?family=Oswald:wght@500;600&family=PT+Sans+Narrow:wght@400;700&family=PT+Sans:wght@400;700&family=Open+Sans:wght@400;600&display=swap">
<style>
  :root {
    --ink-dark: #14060f;
    --teal: #1bb3c8;
    --teal-dark: #0f8fa1;
    --page-bg: #e6e6e4;
    --panel: #f9f9f9;
    --card: #efefef;
    --text: #555;
    --heading-grey: #9a9a9a;
    --footer: #2b2b2b;
    --footer-inner: #232323;
    --ribbon: #c8282c;
  }
  * { box-sizing: border-box; margin: 0; padding: 0; }
  html, body { width: 1200px; height: 1163px; overflow: hidden; }
  body { position: relative; background: var(--page-bg); font-family: "PT Sans", sans-serif; color: var(--text); }
  .abs { position: absolute; }

  .site-header { left: 0; top: 0; width: 1200px; height: 60px; background: var(--ink-dark); }
  .brand { left: 139px; top: 12px; display: flex; align-items: center; gap: 10px; font-family: "PT Sans Narrow", sans-serif; font-weight: 700; font-size: 28px; letter-spacing: 3px; color: var(--teal); text-transform: uppercase; }
  .brand-mark { width: 22px; height: 22px; background: var(--teal); }
  .main-nav { right: 119px; top: 20px; display: flex; gap: 27px; font-family: "PT Sans Narrow", sans-serif; font-size: 15px; text-transform: uppercase; }
  .main-nav a { color: var(--teal); text-decoration: none; }
  .main-nav a.current { color: #fff; }

  .hero-photo { left: 0; top: 60px; width: 1200px; height: 437px;
    background: radial-gradient(ellipse at 60% 70%, #6a7c86 0%, #2f3a42 45%, #151b20 100%); }
  .hero-box { left: 138px; top: 138px; width: 457px; height: 199px; background: rgba(40,40,40,.78); padding: 18px 10px 0 11px; }
  .hero-title { font-family: "Oswald", sans-serif; font-weight: 600; font-size: 42px; line-height: 54px; color: #fff; text-transform: uppercase; letter-spacing: .5px; }
  .hero-rule { margin: 10px 0 10px -2px; border-top: 2px dotted #888; width: 440px; }
  .hero-text { font-size: 11.5px; line-height: 15px; color: #fff; letter-spacing: .4px; }
  .read-more { color: var(--teal); text-decoration: none; }

  .content-panel { left: 140px; top: 435px; width: 940px; height: 670px; background: var(--panel); }
  .intro-bar { left: 140px; top: 435px; width: 940px; height: 62px; background: var(--teal); }
  .intro-text { left: 37px; top: 18px; font-family: "Open Sans", sans-serif; font-size: 21px; letter-spacing: 2.4px; color: #fff; text-transform: uppercase; }
  .intro-divider { left: 660px; top: 8px; height: 46px; border-left: 2px dotted rgba(255,255,255,.7); }
  .signup { left: 677px; top: 14px; width: 227px; height: 34px; border: 2px solid #0e8797; display: flex; background: #fff; }
  .signup-field { flex: 1; font-family: "Open Sans", sans-serif; font-style: italic; font-size: 11px; color: #888; letter-spacing: .8px; padding: 8px 10px; }
  .signup-button { width: 30px; background: var(--ink-dark); display: flex; align-items: center; justify-content: center; }

  .product-card { top: 525px; width: 210px; height: 237px; background: var(--card); text-align: center; overflow: hidden; }
  .product-name { font-family: "Open Sans", sans-serif; font-size: 12px; letter-spacing: 1.2px; color: #444; padding-top: 5px; height: 27px; text-transform: uppercase; }
  .product-photo { margin: 0 auto; width: 196px; height: 140px; }
  .product-caption { font-family: "Open Sans", sans-serif; font-size: 11px; letter-spacing: .6px; margin-top: 9px; color: #555; }
  .more-button { display: inline-block; margin-top: 10px; width: 68px; height: 23px; background: var(--teal); color: #fff; font-family: "Open Sans", sans-serif; font-weight: 600; font-size: 11px; line-height: 23px; letter-spacing: .8px; }
  .carousel-arrow { top: 620px; }
  .ribbon { left: 955px; top: 521px; }

  .about-box { left: 181px; top: 787px; width: 554px; height: 271px; background: var(--card); border-left: 5px solid var(--teal); padding: 14px 18px 0 15px; }
  .about-title { font-family: "Oswald", sans-serif; font-weight: 500; font-size: 24px; letter-spacing: 3px; color: var(--heading-grey); text-transform: uppercase; }
  .about-rule { border-top: 2px dotted #bbb; margin: 10px 0 10px -5px; }
  .about-text { font-family: "Open Sans", sans-serif; font-size: 11.3px; line-height: 25px; letter-spacing: .85px; color: #666; }
  .about-text a { color: var(--teal); text-decoration: none; }

  .contact-head { left: 754px; top: 787px; width: 284px; height: 24px; background: #2a2a2a; color: #fff; font-family: "Open Sans", sans-serif; font-size: 12px; letter-spacing: 1.2px; padding: 4px 10px; text-transform: uppercase; }
  .contact-box { left: 754px; top: 821px; width: 284px; height: 237px; background: var(--card); }
  .contact-lead { left: 14px; top: 11px; font-family: "Open Sans", sans-serif; font-size: 11px; letter-spacing: .8px; color: #666; }
  .field-label { font-family: "Open Sans", sans-serif; font-size: 11px; letter-spacing: .8px; color: #666; }
  .field-box { left: 58px; width: 213px; background: #fff; border: 1px solid #bbb; }
  .send-button { left: 108px; top: 198px; width: 69px; height: 24px; background: var(--teal); color: #fff; font-family: "Open Sans", sans-serif; font-weight: 600; font-size: 11px; letter-spacing: .8px; text-align: center; line-height: 24px; }

  .site-footer { left: 0; top: 1100px; width: 1200px; height: 63px; background: var(--footer); }
  .footer-inner { left: 139px; top: 0; width: 940px; height: 63px; background: var(--footer-inner); }
  .footer-nav { left: 42px; top: 23px; display: flex; gap: 23px; font-family: "PT Sans Narrow", sans-serif; font-size: 12px; }
  .footer-nav a { color: #bbb; text-decoration: none; }
  .footer-nav a.current { color: var(--teal); }
  .copyright { right: 40px; top: 23px; font-family: "PT Sans Narrow", sans-serif; font-size: 12px; color: #bbb; }
  .copyright span { color: var(--teal); }
</style>
</head>
<body>
  <header class="site-header abs">
    <div class="brand abs"><span class="brand-mark"></span>Tesh Kalo Trading Co</div>
    <nav class="main-nav abs">
      <a class="current" href="#">Home</a><a href="#">About</a><a href="#">News</a><a href="#">Products</a><a href="#">Testimonials</a><a href="#">Sale</a><a href="#">Contact</a>
    </nav>
  </header>

  <div class="hero-photo abs" role="img" aria-label="Close-up photo of mixing console knobs in blue, grey and green"></div>
  <section class="hero-box abs">
    <h1 class="hero-title">Connecting Musicians<br>and Manufacturers</h1>
    <div class="hero-rule"></div>
    <p class="hero-text">Lorem ipsum dolor sit amet, consectetur adipiscing elit. Curabitur tellus nisi, lobortis eget tincidunt sit amet Et omnis postulant cum <a class="read-more" href="#">read more ▸</a></p>
  </section>

  <div class="content-panel abs"></div>

  <section class="intro-bar abs">
    <p class="intro-text abs">Introduction message text will go here</p>
    <div class="intro-divider abs"></div>
    <div class="signup abs">
      <span class="signup-field">add your email for updates</span>
      <span class="signup-button"><svg width="10" height="10" viewBox="0 0 10 10"><path d="M1 0 L9 5 L1 10Z" fill="#1bb3c8"/></svg></span>
    </div>
  </section>

  <svg class="carousel-arrow abs" style="left:151px" width="28" height="58" viewBox="0 0 28 58"><path d="M28 0 A29 29 0 0 0 28 58Z" fill="#3a3a3a"/><path d="M10 29 L20 22 L20 36Z" fill="#1bb3c8"/></svg>
  <svg class="carousel-arrow abs" style="left:1039px" width="28" height="58" viewBox="0 0 28 58"><path d="M0 0 A29 29 0 0 1 0 58Z" fill="#3a3a3a"/><path d="M18 29 L8 22 L8 36Z" fill="#1bb3c8"/></svg>

  <article class="product-card abs" style="left:179px">
    <p class="product-name">Product name - 3653GA</p>
    <div class="product-photo" role="img" aria-label="Product photo: wireless microphone pair with receiver" style="background:linear-gradient(#fff,#e7f3f0)"></div>
    <p class="product-caption">Eget tincidunt sit amet</p>
    <span class="more-button">more ▸</span>
  </article>
  <article class="product-card abs" style="left:395px">
    <p class="product-name">Product name - 3653GA</p>
    <div class="product-photo" role="img" aria-label="Product photo: stacked rack power amplifiers" style="background:linear-gradient(#fff,#e6e6e8)"></div>
    <p class="product-caption">Eget tincidunt sit amet</p>
    <span class="more-button">more ▸</span>
  </article>
  <article class="product-card abs" style="left:612px">
    <p class="product-name">Product name - 3653GA</p>
    <div class="product-photo" role="img" aria-label="Product photo: analogue mixing desk" style="background:linear-gradient(#4a5666,#232a33)"></div>
    <p class="product-caption">Eget tincidunt sit amet</p>
    <span class="more-button">more ▸</span>
  </article>
  <article class="product-card abs" style="left:829px">
    <p class="product-name">Product name - 3653GA</p>
    <div class="product-photo" role="img" aria-label="Product photo: powered box mixer" style="background:radial-gradient(circle at 50% 50%,#3a3a3a 0,#2a2a2a 40%,#fff 41%)"></div>
    <p class="product-caption">Eget tincidunt sit amet</p>
    <span class="more-button">more ▸</span>
  </article>
  <svg class="ribbon abs" width="82" height="80" viewBox="0 0 82 80">
    <path d="M4 0 L30 0 L80 50 L80 76Z" fill="#c8282c"/>
    <text x="0" y="0" transform="translate(32 18) rotate(45)" fill="#fff" font-family="Oswald, sans-serif" font-weight="600" font-size="15" letter-spacing="1">NEW</text>
  </svg>

  <section class="about-box abs">
    <h2 class="about-title">A little bit about us</h2>
    <div class="about-rule"></div>
    <p class="about-text">Lorem ipsum dolor sit amet, consectetur adipiscing elit. Curabitur tellus nisi, lobortis eget tincidunt sit amet, tempor quis eros. Cum sociis natoque penatibus et magnis dis <a href="#">parturient montes</a>, nascetur ridiculus mus. Aliquam justo lectus, dignissim in iaculis ac, adipiscing non libero. Aliquam non lectus in est consequat semper. Suspendisse gravida eros <a href="#">ac est placerat</a> convallis. Phasellus sit amet ullamcorper risus. Aliquam et libero viverra tortor mollis varius. Etiam gravida elit in ipsum ultricies ac posuere nisi luctus diculus mus. Aliquam justo lectus, dig. &nbsp;<a href="#">read more ▸</a></p>
  </section>

  <h3 class="contact-head abs">Get in touch for more info</h3>
  <form class="contact-box abs">
    <p class="contact-lead abs">Lorem ipsum dolor sit amet, consectetur</p>
    <span class="field-label abs" style="left:14px;top:43px">Name</span>
    <div class="field-box abs" style="top:38px;height:28px"></div>
    <span class="field-label abs" style="left:15px;top:82px">Email</span>
    <div class="field-box abs" style="top:75px;height:28px"></div>
    <span class="field-label abs" style="left:21px;top:119px">Text</span>
    <div class="field-box abs" style="top:112px;height:72px"></div>
    <span class="send-button abs">send ▸</span>
  </form>

  <footer class="site-footer abs">
    <div class="footer-inner abs">
      <nav class="footer-nav abs">
        <a class="current" href="#">Home</a><a href="#">About</a><a href="#">News</a><a href="#">Products</a><a href="#">Testimonials</a><a href="#">Sale</a><a href="#">Contact</a>
      </nav>
      <p class="copyright abs"><span>Copyright 2012</span> &nbsp;All rights reserved</p>
    </div>
  </footer>
</body>
</html>
```